Business Card for Professional Photographer

I'm looking for an eye catching modern clean design that compliments my logo/ website fonts & colours.
I specialise in architecture, corporate & commercial photography so I'm marketing to professional clients rather than portrait / wedding clients.

I would prefer to not have a solid black design.

My logo brand guide is as follows :

Main front font. : Reislust
Main font colour : #fff
Slogan front font : Ubuntu Bold
Monogram front font : Venti Medium
Container colour : #fff

I need print ready files in pdf .png & .eps formats.

Included in the files below are some screen grabs as reference to font & colours etc.

```html
<!DOCTYPE html>
<html lang="en">
<head>
<meta charset="utf-8">
<title>Clear Angle – Business Card</title>
<link href="https://fonts.googleapis.com/css2?family=Lato:wght@400;700&family=Montserrat:wght@300;500&display=swap" rel="stylesheet">
<style>
  :root {
    --backdrop: #2a2a2b;
    --card: #1b1c1e;
    --card-pattern-light: #242528;
    --card-pattern-dark: #1c1d1f;
    --gold: #d6ab45;
    --white: #f4f4f4;
    --rule: #6b6b6b;
  }
  html, body {
    margin: 0;
    padding: 0;
    width: 1200px;
    height: 1108px;
    overflow: hidden;
    background: var(--backdrop);
  }
  .canvas {
    position: relative;
    width: 1200px;
    height: 1108px;
  }
  .card {
    position: absolute;
    top: 224px;
    width: 420px;
    height: 660px;
    border-radius: 22px;
    background: var(--card);
    box-shadow: 0 18px 40px rgba(0,0,0,.45);
    overflow: hidden;
  }
  .card--front { left: 150px; }
  .card--back  { left: 630px; }

  /* front */
  .brand {
    position: absolute;
    left: 44px;
    top: 130px;
    width: 340px;
  }
  .brand__name {
    font-family: "Montserrat", sans-serif;
    font-weight: 300;
    font-size: 30px;
    letter-spacing: 5px;
    color: var(--white);
    margin: 0;
  }
  .brand__tagline {
    font-family: "Montserrat", sans-serif;
    font-weight: 500;
    font-size: 9.5px;
    letter-spacing: 2.4px;
    color: var(--gold);
    margin: 8px 0 0;
  }
  .person {
    position: absolute;
    left: 0;
    right: 0;
    top: 370px;
    text-align: center;
    font-family: "Lato", sans-serif;
  }
  .person__name {
    margin: 0;
    font-weight: 700;
    font-size: 27px;
    color: var(--gold);
    letter-spacing: .5px;
  }
  .person__role {
    margin: 2px 0 0;
    font-size: 19px;
    color: var(--white);
  }
  .divider {
    display: flex;
    align-items: center;
    justify-content: center;
    gap: 8px;
    margin: 12px 0 14px;
  }
  .divider__line {
    width: 82px;
    height: 1px;
    background: var(--rule);
  }
  .divider__icon {
    width: 26px;
    height: 26px;
  }
  .contact {
    margin: 0;
    padding: 0;
    list-style: none;
    font-size: 20px;
    line-height: 27px;
    color: var(--white);
  }
  .address-rule {
    width: 206px;
    height: 1px;
    background: var(--rule);
    margin: 12px auto 10px;
  }
  .address {
    margin: 0;
    font-style: normal;
    font-size: 20px;
    line-height: 26px;
    color: var(--white);
  }

  /* back */
  .back-pattern {
    position: absolute;
    inset: 0;
    background: linear-gradient(160deg, var(--card-pattern-light), var(--card-pattern-dark));
  }
  .back-mark {
    position: absolute;
    left: 0;
    right: 0;
    top: 470px;
    text-align: center;
    font-family: "Montserrat", sans-serif;
    font-weight: 300;
    font-size: 20px;
    letter-spacing: 4px;
    color: var(--gold);
    margin: 0;
  }
</style>
</head>
<body>
<main class="canvas">

  <section class="card card--front" aria-label="Card front">
    <header class="brand">
      <p class="brand__name">CLEAR ANGLE</p>
      <p class="brand__tagline">Architecture Corporate Commercial</p>
    </header>

    <div class="person">
      <h1 class="person__name">DANIEL HART</h1>
      <p class="person__role">Managing Director</p>

      <div class="divider">
        <span class="divider__line"></span>
        <svg class="divider__icon" viewBox="0 0 26 26" aria-label="Phone">
          <circle cx="13" cy="13" r="13" fill="var(--gold)"/>
          <path d="M8.5 7.5l2.5-.5 1.5 3-1.6 1.2a7 7 0 0 0 3.4 3.4l1.2-1.6 3 1.5-.5 2.5c-5 .6-10-4.4-9.5-9.5z" fill="var(--card)"/>
        </svg>
        <svg class="divider__icon" viewBox="0 0 26 26" aria-label="Email">
          <circle cx="13" cy="13" r="13" fill="var(--gold)"/>
          <rect x="7" y="8.5" width="12" height="9" fill="none" stroke="var(--card)" stroke-width="1.4"/>
          <path d="M7 8.5l6 5 6-5" fill="none" stroke="var(--card)" stroke-width="1.4"/>
        </svg>
        <svg class="divider__icon" viewBox="0 0 26 26" aria-label="Website">
          <circle cx="13" cy="13" r="13" fill="var(--gold)"/>
          <circle cx="13" cy="13" r="6" fill="none" stroke="var(--card)" stroke-width="1.4"/>
          <ellipse cx="13" cy="13" rx="2.6" ry="6" fill="none" stroke="var(--card)" stroke-width="1.2"/>
          <path d="M7 13h12" stroke="var(--card)" stroke-width="1.2"/>
        </svg>
        <span class="divider__line"></span>
      </div>

      <ul class="contact">
        <li>044-555 018 246</li>
        <li>info@clearangle.io</li>
        <li>www.clearangle.studio</li>
      </ul>
      <div class="address-rule"></div>
      <address class="address">27, Mill Street Studio,<br>52190,Eastmoor Vale</address>
    </div>
  </section>

  <section class="card card--back" aria-label="Card back">
    <div class="back-pattern" role="img" aria-label="Faint tone-on-tone repeat of the brand mark across the card"></div>
    <p class="back-mark">CLEAR ANGLE</p>
  </section>

</main>
</body>
</html>
```